Fitness Equipment & Service

I want to make the card eye catching and fun. We are called Corvane Motion Limited and we are based in Wales. We sell, install and service all types of fitness equipment from Skipping ropes, right through the Dumbbells, Kettle bells and Barbells through to state of the art Treadmills, Running Machines and Strength Equipment. We also design and install changing room furniture and lockers.

TYPOGRAPHY
We would like to use Futrura. Futura has an appearance of efficiency and forwardness. The typeface is derived
from simple geometric forms (near-perfect circles, triangles and squares) and is based on strokes of
near-even weight, which are low in contrast. This is most visible in the almost perfectly round stroke of
the o, which is nonetheless slightly ovoid.
The lowercase has tall ascenders, which rise above the cap line. The uppercase
characters present proportions similar to those of classical Roman capitals.

TYPOGRAPHIC CONSIDERATIONS
No Strike though
No Horizontal Scaling
No Drop Shadows
No Effects
Never use less than 120% Leading

OUR CORPORATE COLOURS
BRAND GUIDELINES
We were thinking that our primary colour palette consists of the Acid Green (Pantone 382) and Process Black.

We work closely with tquarly Ltd and would like to include their name on the card somewhere. I have attached images of the other brands that we work with as an idea or the small icons I have included that illustrate what we do?. I have very kindly been given permission to use any of the images off the files that I have included below, so I hope these help. I will include these below. I would be open to suggestions if it made the card more striking Can you do it?
Updates

Hi All, Just wanted to add a few thoughts but you are the guys with the creative visions (thats why are here) We are based in Wales, UK and we would be open to lots of different ideas on a theme but must be eye catching, Bold and FUN. If you can or think that the Welsh or any dragon could be put in there then go for it (its not a must have) We have also added some ideas for colour but again its over to you!! GO FOR IT ! Thanks and look forward to your visions! Owen

Hi All, Just thought I would sen through the contact details that need to be on the card. (if you want to play around with icons instead of the wording twitter, Facebook, go for it): Corvane Motion Limited Owen Pritchard Managing Director Mob: +44 (0)7582 913 406 e-mail: sales@corvanemotion.co.uk Web: Corvanemotion.co.uk twitter: @motionLetterbin Facebook: Corvane Motion Limited

```html
<!DOCTYPE html>
<html lang="en">
<head>
<meta charset="utf-8">
<title>Corvane Motion Limited – Business Card</title>
<link href="https://fonts.googleapis.com/css2?family=Arimo:wght@400;700&family=Tinos:wght@700&display=swap" rel="stylesheet">
<style>
  :root {
    --backdrop: #2b2623;
    --card-black: #17171a;
    --ink-white: #f2f2f2;
    --brand-blue: #1d54a8;
    --tile-blue: #1664bd;
    --tile-mid: #1b5aa6;
    --tile-navy: #143a6b;
    --tile-deep: #0f2d55;
    --tile-cyan: #3bb4e8;
    --tile-grey: #8596a6;
    --tile-pale: #b7c5d2;
    --globe: #1a3d8c;
    --border-white: #ffffff;
  }
  * { margin: 0; padding: 0; box-sizing: border-box; }
  html, body { width: 1200px; height: 780px; overflow: hidden; }
  body { background: var(--backdrop); position: relative; font-family: "Arimo", Arial, sans-serif; }

  .card { position: absolute; top: 235px; width: 540px; height: 310px; }

  /* Front */
  .card-front { left: 40px; background: var(--card-black); color: var(--ink-white); }
  .brand-block { position: absolute; left: 28px; top: 70px; width: 150px; text-align: center; }
  .brand-dot { width: 74px; height: 74px; border-radius: 50%; background: var(--globe); margin: 0 auto 14px; }
  .brand-name { font-size: 15px; font-weight: 700; line-height: 1.25; color: var(--ink-white); }
  .divider { position: absolute; left: 196px; top: 26px; width: 2px; height: 258px; background: var(--ink-white); }
  .person { position: absolute; left: 222px; top: 38px; }
  .person-name { font-family: "Tinos", "Times New Roman", serif; font-weight: 700; font-size: 34px; color: var(--brand-blue); line-height: 1.2; }
  .person-role { font-size: 17px; line-height: 1.3; }
  .contact-list { position: absolute; left: 222px; top: 146px; list-style: none; }
  .contact-item { display: flex; align-items: center; gap: 9px; font-size: 16px; line-height: 1.3; margin-bottom: 3px; }
  .contact-icon { width: 11px; height: 11px; background: var(--brand-blue); flex: none; display: flex; align-items: center; justify-content: center; }

  /* Back */
  .card-back { left: 620px; background: var(--border-white); padding: 9px; }
  .back-field { position: relative; width: 100%; height: 100%; overflow: hidden; background: var(--tile-blue); }
  .photo-fill { position: absolute; inset: 0; background: radial-gradient(ellipse at 68% 55%, #0d2547 0%, #17427d 38%, #1664bd 75%); }
  .tile-grid { position: absolute; inset: 0; display: grid; grid-template-columns: repeat(8, 1fr); grid-template-rows: repeat(5, 1fr); }
  .tile { background: transparent; }
  .tile--mid { background: var(--tile-mid); }
  .tile--cyan { background: var(--tile-cyan); }
  .tile--grey { background: var(--tile-grey); }
  .tile--pale { background: var(--tile-pale); }
  .tile--navy { background: var(--tile-navy); }
  .tile--deep { background: var(--tile-deep); }
  .tile--blue { background: var(--tile-blue); }
  .back-brand { position: absolute; left: 26px; top: 150px; display: flex; align-items: center; gap: 10px; }
  .back-brand .brand-dot { width: 60px; height: 60px; margin: 0; }
  .back-brand .brand-name { font-size: 14px; text-align: left; }
</style>
</head>
<body>

<section class="card card-front" aria-label="Card front">
  <div class="brand-block">
    <div class="brand-dot"></div>
    <p class="brand-name">Corvane Motion Limited</p>
  </div>
  <div class="divider"></div>
  <div class="person">
    <h1 class="person-name">Owen Pritchard</h1>
    <p class="person-role">Managing Director</p>
  </div>
  <ul class="contact-list">
    <li class="contact-item">
      <span class="contact-icon">
        <svg width="8" height="8" viewBox="0 0 10 10"><path d="M2 1l2 2-1 1.5c.8 1.4 1.6 2.2 3 3L7.5 6l2 2-1.5 1.5C4.5 9 1 5.5.5 2.5z" fill="#fff"/></svg>
      </span>+44 (0)7582 913 406
    </li>
    <li class="contact-item"><span class="contact-icon"></span>@motionLetterbin</li>
    <li class="contact-item"><span class="contact-icon"></span>Corvanemotion.co.uk</li>
    <li class="contact-item"><span class="contact-icon"></span>Corvane Motion Limited</li>
    <li class="contact-item"><span class="contact-icon"></span>sales@corvanemotion.co.uk</li>
  </ul>
</section>

<section class="card card-back" aria-label="Card back">
  <div class="back-field">
    <div class="photo-fill" role="img" aria-label="Blue-tinted photograph of a dumbbell behind a grid of fitness equipment icons"></div>
    <div class="tile-grid">
      <div class="tile tile--mid"></div><div class="tile tile--cyan"></div><div class="tile"></div><div class="tile"></div><div class="tile"></div><div class="tile"></div><div class="tile"></div><div class="tile"></div>
      <div class="tile"></div><div class="tile tile--grey"></div><div class="tile tile--blue"></div><div class="tile"></div><div class="tile tile--navy"></div><div class="tile tile--blue"></div><div class="tile"></div><div class="tile"></div>
      <div class="tile"></div><div class="tile"></div><div class="tile tile--pale"></div><div class="tile"></div><div class="tile"></div><div class="tile"></div><div class="tile"></div><div class="tile tile--navy"></div>
      <div class="tile"></div><div class="tile"></div><div class="tile tile--grey"></div><div class="tile"></div><div class="tile tile--blue"></div><div class="tile"></div><div class="tile tile--deep"></div><div class="tile"></div>
      <div class="tile"></div><div class="tile"></div><div class="tile"></div><div class="tile tile--navy"></div><div class="tile"></div><div class="tile tile--navy"></div><div class="tile"></div><div class="tile"></div>
    </div>
    <div class="back-brand">
      <div class="brand-dot"></div>
      <p class="brand-name">Corvane Motion<br>Limited</p>
    </div>
  </div>
</section>

</body>
</html>
```